Business Card Design for Software Development Company

I am looking for a business card design the incorporates my new logo (attached below).

Key information to include:
Name: Martin Quelbrook
Title: CEO
Email: martin@brightwellcivic.example
Phone: 555-218-9403
Website: www.brightwellcivic.example

NOTE: This design should be easy to edit so that we can order cards for different members of our team.

```html
<!DOCTYPE html>
<html lang="en">
<head>
<meta charset="utf-8">
<title>Brightwell Labs Business Card</title>
<link rel="stylesheet" href="https://fonts.googleapis.com/css2?family=Montserrat:wght@400;700&display=swap">
<style>
  :root {
    --backdrop: #1a1a1a;
    --card: #232323;
    --teal: #13ae98;
    --orange: #e9812a;
    --rule: #d9a25c;
    --ink: #f3f3f3;
    --muted: #d8d8d8;
    --haze-teal: rgba(19, 174, 152, 0.10);
    --haze-brown: rgba(150, 90, 50, 0.10);
  }
  * { margin: 0; padding: 0; box-sizing: border-box; }
  html, body { width: 1200px; height: 1059px; overflow: hidden; }
  body {
    background: var(--backdrop);
    font-family: "Montserrat", Arial, sans-serif;
    position: relative;
  }
  .card {
    position: absolute;
    background: var(--card);
    border-radius: 18px;
    overflow: hidden;
  }
  .card-front { left: 257px; top: 89px; width: 687px; height: 390px; }
  .card-back { left: 254px; top: 546px; width: 693px; height: 394px; }

  .company {
    position: absolute;
    display: flex;
    align-items: center;
    gap: 10px;
    font-weight: 700;
    color: var(--ink);
    line-height: 1;
    white-space: nowrap;
  }
  .company-square { background: var(--teal); flex: none; }

  .card-front .company { right: 42px; top: 62px; font-size: 32px; }
  .card-front .company-square { width: 16px; height: 16px; }

  .card-back .company {
    left: 50%; top: 50%;
    transform: translate(-50%, -50%);
    font-size: 52px; gap: 14px;
  }
  .card-back .company-square { width: 24px; height: 24px; }

  .back-haze {
    position: absolute; left: 0; top: 0;
    width: 434px; height: 394px;
    background: linear-gradient(160deg, var(--haze-teal) 0%, var(--haze-brown) 55%, rgba(35, 35, 35, 0) 100%);
  }

  .name-marker {
    position: absolute; left: 0; top: 224px;
    width: 17px; height: 38px; background: var(--teal);
  }
  .person { position: absolute; left: 42px; top: 220px; }
  .person-name { font-size: 25px; font-weight: 700; letter-spacing: 0.8px; line-height: 1.1; }
  .person-name .first { color: var(--teal); }
  .person-name .last { color: var(--orange); }
  .person-title { font-size: 17px; color: var(--muted); letter-spacing: 0.5px; margin-top: 1px; }

  .divider {
    position: absolute; left: 42px; right: 42px; top: 282px;
    height: 1px; background: var(--rule);
  }
  .contact {
    position: absolute;
    display: flex; align-items: center; gap: 7px;
    font-size: 17px; color: var(--ink); letter-spacing: 0.3px;
  }
  .contact svg { width: 12px; height: 12px; fill: var(--orange); flex: none; }
  .contact-phone { left: 42px; top: 300px; }
  .contact-email { left: 42px; top: 328px; }
  .contact-web { right: 42px; top: 328px; }

  .accent-band {
    position: absolute; right: 43px; bottom: 0;
    width: 228px; height: 12px; background: var(--teal);
  }
</style>
</head>
<body>
  <section class="card card-front">
    <div class="company"><span class="company-square"></span>Brightwell Labs</div>

    <div class="name-marker"></div>
    <div class="person">
      <div class="person-name"><span class="first">MARTIN</span> <span class="last">QUELBROOK</span></div>
      <div class="person-title">CEO</div>
    </div>

    <div class="divider"></div>

    <div class="contact contact-phone">
      <svg viewBox="0 0 12 12" aria-hidden="true"><path d="M1 4.5C1 2.5 3 1.5 6 1.5S11 2.5 11 4.5L8.6 5 8.2 3.8H3.8L3.4 5ZM3 5.5h6l1.5 5h-9Z"/></svg>
      <span>555-218-9403</span>
    </div>
    <div class="contact contact-email">
      <svg viewBox="0 0 12 12" aria-hidden="true"><path d="M1 5 6 1.5 11 5v6H1Zm1.2.6L6 8.4l3.8-2.8-3.8-2.6Z"/></svg>
      <span>martin@brightwellcivic.example</span>
    </div>
    <div class="contact contact-web">
      <svg viewBox="0 0 12 12" aria-hidden="true"><circle cx="6" cy="6" r="5.5"/><path d="M3 3.5c1 0 1.6.8 1.2 1.8S5 7 6 7.2 6.6 9.5 5.6 10.5M8 2.2c-.4 1 .2 1.6 1.2 1.8s1.4 1.6.8 2.6" stroke="#232323" stroke-width="1" fill="none"/></svg>
      <span>www.brightwellcivic.example</span>
    </div>

    <div class="accent-band"></div>
  </section>

  <section class="card card-back">
    <div class="back-haze" role="img" aria-label="Faint enlarged brand symbol in muted teal and brown"></div>
    <div class="company"><span class="company-square"></span>Brightwell Labs</div>
  </section>
</body>
</html>
```